Brimsett Gardening Fresh New Website

We are looking to create a simple fresh website for our landscaping business. The website should appeal to a 'high end' audience. We deal with a lot of Embassies and affluent clients who have extremely large gardens that are meticulously maintained. The site is about communicating our excellent landscaping and customer service skills and encouraging new clients to reach out and engage us to take care of their gardens.

The website is basically going to be our business card, it will have almost no functionality other than two 'contact us' forms, one for smaller clients and one for more detailed projects.

The website will not have a lot of written content and will have to show photos of beautifully landscaped gardens.

The main logo in black will influence the site, however, we are open to all suggestions.

We are expecting to have the following pages:
Home Page
Services
About Us
Contact Us
Showcase (photo gallery of our work)

We need someone who can code it to wordpress and be available for minor changes over a number of days. They will be simple tweaks.

```html
<!DOCTYPE html>
<html lang="en">
<head>
<meta charset="utf-8">
<title>Brimsett Gardening</title>
<link href="https://fonts.googleapis.com/css2?family=Cinzel:wght@400;500&family=Poppins:wght@400;500;600;700&display=swap" rel="stylesheet">
<style>
:root{
  --dark:#1d1b18;
  --gold:#a8772a;
  --yellow:#f6c92a;
  --soft-yellow:#f0d23e;
  --ink:#1e1e1e;
  --text:#4a4a4a;
  --light:#f4f4f4;
  --white:#ffffff;
  --line:#dcdcdc;
}
*{margin:0;padding:0;box-sizing:border-box}
html,body{width:1200px;height:3896px;overflow:hidden}
body{position:relative;font-family:"Poppins",sans-serif;color:var(--text);background:var(--white)}
.serif{font-family:"Cinzel",serif;font-weight:400}
.btn{position:absolute;display:flex;align-items:center;justify-content:center;background:var(--gold);color:var(--white);font-size:12px;font-weight:500;letter-spacing:.3px;text-transform:uppercase;border-radius:2px}
.rule{position:absolute;height:2px;width:50px;background:var(--gold)}

/* header */
.site-header{position:absolute;left:0;top:0;width:1200px;height:85px;background:var(--dark)}
.brand{position:absolute;left:141px;top:28px;display:flex;align-items:center;gap:8px;color:var(--gold);font-size:13px;font-weight:500;letter-spacing:2px}
.brand i{display:block;width:12px;height:12px;border:1.5px solid var(--gold);border-radius:50%}
.nav a{position:absolute;top:33px;font-size:13px;color:var(--white);text-decoration:none}
.nav a.active{color:var(--yellow)}

/* hero */
.hero-photo{position:absolute;left:0;top:85px;width:1200px;height:550px;background:linear-gradient(100deg,#5b5444 0%,#7a6f58 25%,#5e6b46 45%,#3f5b2e 70%,#2f4a26 100%)}
.hero-photo::after{content:"";position:absolute;inset:0;background:linear-gradient(180deg,rgba(0,0,0,.05),rgba(0,0,0,.25))}
.hero-tag{position:absolute;left:141px;top:257px;width:272px;height:53px;background:var(--white);display:flex;align-items:center;justify-content:center;font-size:22px;font-weight:700;color:var(--ink)}
.hero-title{position:absolute;left:141px;top:318px;font-size:40px;line-height:46px;color:var(--white)}

.quick{position:absolute;left:710px;top:107px;width:349px;height:503px;background:rgba(240,240,236,.82)}
.tabs{position:absolute;left:13px;top:3px;width:320px;height:31px}
.tab{position:absolute;top:0;height:31px;display:flex;align-items:center;justify-content:center;font-size:11px;font-weight:600;text-transform:uppercase}
.tab.on{left:0;width:175px;background:var(--yellow);color:var(--ink);border-radius:16px 0 0 16px}
.tab.off{left:160px;width:160px;background:var(--gold);color:var(--white);clip-path:polygon(10% 0,100% 0,100% 100%,0 100%);padding-left:12px;border-radius:0 16px 0 0}
.quick h3{position:absolute;left:0;top:48px;width:100%;text-align:center;font-size:18px;color:var(--ink)}
.field{position:absolute;left:17px;width:316px;background:var(--white);border:1px solid var(--line);border-radius:3px;font-size:11px;color:#777;padding:0 10px;display:flex;align-items:center;justify-content:space-between}
.field svg{width:14px;height:14px;stroke:#aaa;fill:none;stroke-width:1.3}
.field.msg{align-items:flex-start;padding-top:12px}
.check{position:absolute;display:flex;align-items:center;gap:7px;font-size:10px;color:#333}
.check b{display:block;width:12px;height:12px;background:var(--white);border:1px solid #bbb;border-radius:2px}
.check b.ticked{background:var(--yellow);border-color:var(--gold);position:relative}
.check b.ticked::after{content:"";position:absolute;left:3px;top:0;width:4px;height:7px;border:solid var(--ink);border-width:0 1.5px 1.5px 0;transform:rotate(45deg)}
.submit{left:727px;top:558px;width:316px;height:38px;font-size:14px}

/* about */
.about-photo{position:absolute;left:121px;top:648px;width:484px;height:464px;background:radial-gradient(ellipse at 50% 45%,#b9bdc2 0%,#cdd2cf 40%,#e9ece6 70%,#ffffff 100%)}
.about-title{position:absolute;left:611px;top:752px;font-size:34px;line-height:40px;color:var(--ink)}
.about-title span{color:var(--gold)}
.about p{position:absolute;left:611px;width:450px;font-size:13px;line-height:22px;color:var(--text)}

/* services */
.services{position:absolute;left:0;top:1173px;width:1200px;height:945px;background:var(--light)}
.sec-title{position:absolute;left:0;width:1200px;text-align:center;font-size:36px;color:var(--ink)}
.svc-tab{position:absolute;top:1327px;width:159px;height:35px;display:flex;align-items:center;justify-content:center;font-size:12px;font-weight:500;border-radius:2px}
.card{position:absolute;width:300px;height:241px;border-radius:3px;overflow:hidden}
.card .label{position:absolute;left:0;right:0;bottom:34px;display:flex;justify-content:center;align-items:center;gap:8px;color:var(--white);font-size:15px;font-weight:600}
.card .label svg{width:36px;height:36px;fill:none;stroke:var(--yellow);stroke-width:2}
.card .est{position:absolute;left:106px;bottom:18px;color:var(--white);font-size:12px;text-decoration:underline}
.shade{position:absolute;inset:0;background:linear-gradient(180deg,rgba(0,0,0,0) 45%,rgba(0,0,0,.7))}

/* testimonials */
.reviews{position:absolute;left:0;top:2118px;width:1200px;height:533px;background:linear-gradient(180deg,#4b4a44,#3d4433 60%,#2f3a2b)}
.review{position:absolute;background:var(--white);border-radius:3px;padding:22px 22px}
.review .who{display:flex;align-items:center;gap:10px;margin-bottom:16px}
.avatar{width:58px;height:58px;border-radius:50%;background:linear-gradient(135deg,#9bb6c9,#5e7f93)}
.who strong{display:block;font-size:16px;font-weight:500;color:var(--ink)}
.stars{color:var(--yellow);font-size:14px;letter-spacing:2px}
.review p{font-size:13px;line-height:22px;color:var(--text)}
.review.mid{border-bottom:6px solid var(--gold)}
.arrow{position:absolute;width:44px;height:44px;border:1.5px solid var(--white);border-radius:50%;display:flex;align-items:center;justify-content:center}
.arrow svg{width:16px;height:16px;stroke:var(--white);fill:none;stroke-width:2.5}

/* gallery */
.shot{position:absolute;width:300px}
.shot.hover{background:var(--soft-yellow);display:flex;align-items:center;justify-content:center;text-align:center;padding:0 55px;font-size:13px;line-height:22px;color:var(--ink)}

/* footer */
.site-footer{position:absolute;left:0;top:3519px;width:1200px;height:377px;background:var(--dark);color:var(--white)}
.foot-brand{position:absolute;left:131px;top:118px;width:206px;text-align:center;color:var(--gold);font-size:22px;letter-spacing:4px;line-height:30px;font-weight:500}
.foot-brand i{display:block;width:30px;height:30px;margin:0 auto 16px;border:2px solid var(--gold);border-radius:50%}
.social{position:absolute;top:250px;width:26px;height:26px;border:1.5px solid var(--white);border-radius:50%}
.foot-head{position:absolute;top:56px;font-size:16px;letter-spacing:.5px;padding-bottom:8px}
.foot-head::after{content:"";position:absolute;left:0;bottom:0;width:135px;height:1px;background:rgba(255,255,255,.45)}
.foot-link{position:absolute;left:517px;font-size:12px;color:var(--white)}
.contact-row{position:absolute;left:849px;display:flex;gap:10px;font-size:12px;line-height:18px}
.contact-row svg{width:28px;height:28px;stroke:var(--white);fill:none;stroke-width:1.4;flex:none}
.contact-row strong{font-weight:500}
.foot-rule{position:absolute;left:141px;top:335px;width:918px;height:1px;background:rgba(255,255,255,.3)}
.copy{position:absolute;left:0;top:348px;width:1200px;text-align:center;font-size:12px}
</style>
</head>
<body>

<header class="site-header">
  <div class="brand"><i></i>BRIMSETT GARDENING</div>
  <nav class="nav">
    <a class="active" style="left:434px">Home</a>
    <a style="left:513px">About Us</a>
    <a style="left:613px">Services</a>
    <a style="left:706px">Gallery</a>
    <a style="left:791px">Contact Us</a>
  </nav>
  <div class="btn" style="left:905px;top:24px;width:154px;height:35px;font-size:12px">Request a Quote</div>
</header>

<section class="hero">
  <div class="hero-photo" role="img" aria-label="Large suburban house with stone facade and trimmed hedges in the front garden"></div>
  <div class="hero-tag">BRIMSETT GARDENING</div>
  <h1 class="hero-title serif">YOUR FULL LANDSCAPING<br>&amp; LAWN CARE EXPERTS</h1>
  <div class="btn" style="left:141px;top:430px;width:154px;height:33px">Request a Quote</div>

  <form class="quick">
    <div class="tabs">
      <div class="tab on">Smaller Clients</div>
      <div class="tab off">Large Clients</div>
    </div>
    <h3 class="serif">QUICK CONTACT</h3>
    <div class="field" style="top:83px;height:40px">Name<svg viewBox="0 0 16 16"><circle cx="8" cy="5" r="3"/><path d="M2 15c0-4 12-4 12 0"/></svg></div>
    <div class="field" style="top:132px;height:39px">Email<svg viewBox="0 0 16 16"><rect x="2" y="4" width="12" height="9"/><path d="M2 4l6 5 6-5"/></svg></div>
    <div class="field" style="top:180px;height:40px">Phone<svg viewBox="0 0 16 16"><path d="M4 2l3 3-2 2c1 2 2 3 4 4l2-2 3 3-2 2C7 14 2 9 2 4z"/></svg></div>
    <div class="field" style="top:227px;height:40px">Service Type<svg viewBox="0 0 16 16"><path d="M5 7l3 3 3-3"/></svg></div>
    <div class="field msg" style="top:276px;height:100px">Message</div>
    <div class="check" style="left:17px;top:386px"><b></b>Weekly Lawn Maintenance</div>
    <div class="check" style="left:229px;top:386px"><b></b>Spring Clean Up</div>
    <div class="check" style="left:17px;top:408px"><b class="ticked"></b>Fertilizer/weed Control</div>
    <div class="check" style="left:229px;top:408px"><b></b>Fall Clean Up</div>
    <div class="check" style="left:17px;top:431px"><b></b>Core Aeration</div>
  </form>
  <div class="btn submit">Submit</div>
</section>

<section class="about">
  <div class="about-photo" role="img" aria-label="White two-storey house with wraparound porch and lawn, fading softly into white"></div>
  <h2 class="about-title serif"><span>ABOUT</span><br>BRIMSETT GARDENING</h2>
  <div class="rule" style="left:611px;top:843px"></div>
  <p style="top:862px">Duis aute irure dolor in reprehenderit in voluptate velit esse cillum dolore eu fugiat nulla pariatur.</p>
  <p style="top:912px">Lorem ipsum dolor sit amet, consectetur adipiscing elit, sed do eiusmod tempor incididunt ut labore et dolore magna aliqua. Ut enim ad minim veniam, quis nostrud exercitation ullamco laboris nisi ut aliquip ex ea commodo consequat.</p>
  <div class="btn" style="left:611px;top:1021px;width:153px;height:34px">Read More</div>
</section>

<section class="services"></section>
<h2 class="sec-title serif" style="top:1248px">OUR SERVICES</h2>
<div class="rule" style="left:575px;top:1303px"></div>
<div class="svc-tab" style="left:437px;background:var(--yellow);color:var(--ink)">LANDSCAPE SERVICE</div>
<div class="svc-tab" style="left:602px;background:var(--gold);color:var(--white)">LAWN SERVICE</div>

<div class="card" style="left:141px;top:1393px;background:linear-gradient(180deg,#6f9fd0,#8fb3c9 35%,#3f5d2c 60%,#2b3d1f)" role="img" aria-label="Large estate house behind mature trees and green lawn">
  <div class="shade"></div>
  <div class="label"><svg viewBox="0 0 36 36"><rect x="4" y="4" width="12" height="28"/><rect x="20" y="4" width="12" height="12"/><path d="M20 22h12v10H20z"/></svg>Design Service</div>
</div>
<div class="card" style="left:449px;top:1393px;background:linear-gradient(180deg,#7d8d6a,#4e6a37 50%,#2d3f20)" role="img" aria-label="Wooded garden with mulched beds and small shed">
  <div class="shade"></div>
  <div class="label" style="bottom:44px"><svg viewBox="0 0 36 36"><path d="M2 10l8 4 14 0 6 10"/><circle cx="26" cy="28" r="5"/><path d="M10 14l4 12h8"/></svg>Mulch or Rock Install</div>
  <div class="est">Get A Estimate →</div>
</div>
<div class="card" style="left:758px;top:1393px;background:linear-gradient(160deg,#4a3a2c,#3a2d22 50%,#2a211a)" role="img" aria-label="Dark soil with terracotta pots and a red garden trowel">
  <div class="shade"></div>
  <div class="label"><svg viewBox="0 0 36 36"><path d="M4 32h28M8 32l6-10 8 4 6-14"/><path d="M24 6l6 6"/></svg>Grading Rough</div>
</div>
<div class="card" style="left:141px;top:1710px;background:linear-gradient(180deg,#5d7046,#8a9a86 30%,#3f6628 60%,#25391a)" role="img" aria-label="Grand white country house with broad lawn">
  <div class="shade"></div>
  <div class="label"><svg viewBox="0 0 36 36"><rect x="8" y="5" width="20" height="27" rx="2"/><path d="M12 12h12M12 18h12M12 24h8"/></svg>Grading Final</div>
</div>
<div class="card" style="left:449px;top:1710px;background:linear-gradient(180deg,#3b6ea0,#4f6a2f 30%,#6b5a3c 55%,#3c5522)" role="img" aria-label="Workers unrolling fresh sod onto soil">
  <div class="shade"></div>
  <div class="label"><svg viewBox="0 0 36 36"><rect x="6" y="4" width="24" height="28" rx="2"/><circle cx="14" cy="22" r="4"/><circle cx="23" cy="14" r="3"/></svg>Sod Installation</div>
</div>
<div class="card" style="left:758px;top:1710px;background:linear-gradient(180deg,#a9b6a7,#4f6b36 40%,#2e4a20)" role="img" aria-label="Hedged front garden with low retaining wall and black railing">
  <div class="shade"></div>
  <div class="label"><svg viewBox="0 0 36 36"><path d="M3 8h30v22H3zM3 15h30M3 22h30M12 8v7M24 8v7M18 15v7M8 22v8M28 22v8"/></svg>Retaining Walls</div>
</div>
<div class="btn" style="left:522px;top:1999px;width:154px;height:35px">Request a Quote</div>

<section class="reviews" role="img" aria-label="Dimmed garden scene with trees and a picnic table behind the reviews"></section>
<h2 class="sec-title serif" style="top:2192px;color:var(--white)">WHAT OUR CLIENTS SAY</h2>
<div class="rule" style="left:575px;top:2250px"></div>

<div class="review" style="left:141px;top:2300px;width:299px;height:268px">
  <div class="who"><div class="avatar" role="img" aria-label="Client portrait"></div><div><strong>Owen Hartley</strong><span class="stars">★★★★★</span></div></div>
  <p>Lorem ipsum dolor sit amet, consectetur adipiscing elit, sed do eiusmod tempor incididunt ut labore et dolore magna aliqua. Ut enim ad minim veniam ut aut reiciendis voluptatibus maiores alias ut aut reiciendis voluptatibus.</p>
</div>
<div class="review mid" style="left:449px;top:2271px;width:300px;height:282px">
  <div class="who"><div class="avatar" role="img" aria-label="Client portrait"></div><div><strong>Clara Bennet</strong><span class="stars">★★★★★</span></div></div>
  <p>Sed ut perspiciatis unde omnis iste natus error sit voluptatem accusantium doloremque laudantium, totam rem aperiam, eaque ipsa quae ab illo AMIT inventore veritatis et quasi architecto beatae vitae dicta sunt explicabo. Nemo enim ipsam voluptatem.</p>
</div>
<div class="review" style="left:759px;top:2300px;width:300px;height:268px">
  <div class="who"><div class="avatar" role="img" aria-label="Client portrait"></div><div><strong>Noah R</strong><span class="stars">★★★★★</span></div></div>
  <p>Lorem ipsum dolor sit amet, consectetur adipiscing elit, sed do eiusmod tempor incididunt ut labore et dolore magna aliqua. Ut enim ad minim veniam ut aut reiciendis voluptatibus maiores alias ut aut reiciendis voluptatibus.</p>
</div>
<div class="arrow" style="left:75px;top:2431px"><svg viewBox="0 0 16 16"><path d="M10 3L5 8l5 5"/></svg></div>
<div class="arrow" style="left:1082px;top:2431px"><svg viewBox="0 0 16 16"><path d="M6 3l5 5-5 5"/></svg></div>

<section class="gallery">
  <h2 class="sec-title serif" style="top:2726px">WORK GALLERY</h2>
  <div class="rule" style="left:575px;top:2781px"></div>
  <div class="shot" style="left:141px;top:2834px;height:268px;background:linear-gradient(180deg,#c9cdd2,#d9c9a8 40%,#7a8a5a 70%,#5a7036)" role="img" aria-label="Cottage with stone walls and purple flowering garden"></div>
  <div class="shot" style="left:141px;top:3109px;height:267px;background:linear-gradient(180deg,#9fb08a,#4d6a2e 45%,#8a8478 75%,#5a5a4e)" role="img" aria-label="Stone fire pit surrounded by trees and garden benches"></div>
  <div class="shot hover" style="left:449px;top:2805px;height:268px">Itaque earum rerum hic tenetur a sapiente delectus, ut aut reiciendis voluptatibus maiores alias consequatur aut perferendis doloribus asperiores repellat.</div>
  <div class="shot" style="left:449px;top:3080px;height:268px;background:linear-gradient(180deg,#4a6a2c,#a04a4a 30%,#7a6e62 60%,#6a5c50)" role="img" aria-label="Stone garden path with red and pink flower beds"></div>
  <div class="shot" style="left:759px;top:2834px;height:268px;background:linear-gradient(180deg,#a9c3d6,#7d8d5c 45%,#8dba3a 70%,#6e9a2a)" role="img" aria-label="Sunlit green lawn sloping up to a villa among palms"></div>
  <div class="shot" style="left:759px;top:3109px;height:267px;background:linear-gradient(180deg,#c3ccd0,#4f6e2f 40%,#8a8170 70%,#5b8a2c)" role="img" aria-label="Chequered stepping stone path leading to a house"></div>
  <div class="btn" style="left:522px;top:3400px;width:154px;height:33px">View All</div>
</section>

<footer class="site-footer">
  <div class="foot-brand"><i></i>BRIMSETT<br>GARDENING</div>
  <span class="social" style="left:169px" aria-label="Social profile"></span>
  <span class="social" style="left:205px" aria-label="Social profile"></span>
  <span class="social" style="left:240px" aria-label="Social profile"></span>
  <span class="social" style="left:273px" aria-label="Social profile"></span>

  <div class="foot-head serif" style="left:517px">QUICK LINKS</div>
  <span class="foot-link" style="top:104px">Home</span>
  <span class="foot-link" style="top:145px">Services</span>
  <span class="foot-link" style="top:185px">Gallery</span>
  <span class="foot-link" style="top:226px">About Us</span>
  <span class="foot-link" style="top:267px">contact Us</span>

  <div class="foot-head serif" style="left:849px">CONTACT DETAILS</div>
  <div class="contact-row" style="top:98px"><svg viewBox="0 0 28 28"><circle cx="14" cy="14" r="11"/><path d="M14 8c-3 0-5 2-5 5 0 4 5 8 5 8s5-4 5-8c0-3-2-5-5-5z"/></svg><span>48 Larkfield Row, Unit 2<br>Ashbury, ST 40918</span></div>
  <div class="contact-row" style="top:170px"><svg viewBox="0 0 28 28"><path d="M5 4l5 5-3 3c2 4 5 7 9 9l3-3 5 5-3 3C12 25 3 16 3 7z"/></svg><span><strong>Phone</strong><br>(555) 214-3086</span></div>
  <div class="contact-row" style="top:243px"><svg viewBox="0 0 28 28"><rect x="3" y="7" width="22" height="16"/><path d="M3 7l11 9 11-9"/></svg><span><strong>Email</strong><br>info@brimsettgardening.com</span></div>

  <div class="foot-rule"></div>
  <div class="copy">© 2024 Brimsett Gardening. All Rights Reserved</div>
</footer>

</body>
</html>
```